Stationery Design Task - Stationary, memo and report templates for professional services company

Looking for someone to update stationary design but just as importantly come up with a template for reports and memos for use in our consulting firm. Would also like some brand use guidelines to be able to share with our whole team. We have an existing logo that we like. Need to update with a more contemporary look so that our deliverables to clients look good and professional yet stylish. This is for business to business communications. No need for envelope design. Important to have design for multiple pages, i.e. first page of a report and then 2nd page. Need to use in MS word documents so must be easy to use and replicate. Don't want something overly complex. Clean, fresh looking is best.

Industry/Entity Type

Information Technology

Font styles to use
Sans Serif

Colors
33a6d7
0792cd
85cae6
cee9f5
cedeed
85abd2
3377b5
0455a3

Requirements
Must have
• Clean look but with a little style or pop. Something that can easily be used in word documents. Need to have page styles that have a first page of a report (not a cover page) and then secondary page.
Nice to have
• - Although the dark blue is our primary color. Might be willing to look at some accent color as well.
Should not have
• Not just our logo on the page with a color bar.

```html
<!DOCTYPE html>
<html lang="en">
<head>
<meta charset="utf-8">
<title>Northvale Systems – Stationery Set</title>
<link rel="stylesheet" href="https://fonts.googleapis.com/css2?family=Roboto:wght@400;500;700&family=Poppins:wght@400;700&family=Didact+Gothic&display=swap">
<style>
  :root {
    --bg: #676767;
    --paper: #ffffff;
    --blue-primary: #0792cd;
    --blue-deep: #0455a3;
    --blue-mid: #3377b5;
    --blue-cover-top: #0a7fc6;
    --blue-cover-bottom: #0565a6;
    --blue-pale: #cee9f5;
    --ink: #3c3c3c;
    --ink-soft: #666666;
    --rule: #6f6f6f;
  }
  * { box-sizing: border-box; margin: 0; padding: 0; }
  html, body { width: 1200px; height: 578px; overflow: hidden; }
  body { background: var(--bg); position: relative; font-family: "Didact Gothic", sans-serif; color: var(--ink); }

  .page {
    position: absolute; top: 52px; width: 337px; height: 475px;
    background: var(--paper); overflow: hidden;
  }
  .page--cover { left: 62px; }
  .page--letter { left: 434px; }
  .page--continuation { left: 806px; }

  /* Cover */
  .cover-band { position: absolute; inset: 0; width: 337px; height: 475px; }
  .cover-brand {
    position: absolute; left: 100px; top: 52px; display: flex; align-items: center; gap: 12px;
  }
  .cover-brand__dot { width: 36px; height: 36px; border-radius: 50%; background: var(--paper); }
  .cover-brand__name {
    font-family: "Roboto", sans-serif; font-weight: 700; color: var(--paper);
    font-size: 17px; line-height: 1.05; letter-spacing: 0.5px; width: 130px;
  }
  .cover-title {
    position: absolute; right: 39px; top: 118px; text-align: right;
    font-family: "Roboto", sans-serif; font-weight: 700; color: var(--paper);
    font-size: 33px; line-height: 36px;
  }
  .cover-subtitle {
    position: absolute; right: 39px; top: 195px;
    font-family: "Roboto", sans-serif; font-weight: 500; color: var(--paper); font-size: 12.5px;
  }
  .cover-credit { position: absolute; left: 26px; top: 387px; width: 165px; }
  .cover-credit__label { font-family: "Poppins", sans-serif; font-weight: 700; color: var(--blue-primary); font-size: 11px; letter-spacing: 0.2px; line-height: 14px; }
  .cover-credit__name { font-family: "Poppins", sans-serif; color: var(--ink-soft); font-size: 10px; line-height: 14px; }
  .cover-dates {
    margin-top: 10px; border-top: 1px solid var(--rule); border-bottom: 1px solid var(--rule);
    display: flex; gap: 22px; padding: 6px 0 6px;
  }
  .cover-dates__label { font-family: "Poppins", sans-serif; color: var(--blue-primary); font-size: 7.8px; line-height: 10px; }
  .cover-dates__value { font-family: "Poppins", sans-serif; color: var(--ink); font-size: 7.8px; line-height: 10px; }

  /* Letterhead */
  .letterhead { position: absolute; left: 30px; top: 22px; width: 290px; height: 50px; }
  .letterhead__dot { position: absolute; left: 0; top: 0; width: 38px; height: 38px; border-radius: 50%; background: var(--blue-primary); }
  .letterhead__name {
    position: absolute; left: 60px; top: 3px;
    font-family: "Roboto", sans-serif; font-weight: 700; color: var(--blue-primary); font-size: 12px; letter-spacing: 0.3px;
  }
  .letterhead__address {
    position: absolute; left: 60px; top: 22px; font-family: "Roboto", sans-serif;
    font-size: 5.4px; line-height: 8.6px; color: var(--ink); letter-spacing: 0.2px;
  }
  .letterhead__contact { position: absolute; left: 192px; top: 17px; list-style: none; }
  .letterhead__contact li {
    display: flex; align-items: center; gap: 3px; font-family: "Roboto", sans-serif;
    font-size: 5.4px; line-height: 8.6px; color: var(--ink); letter-spacing: 0.2px;
  }
  .contact-icon {
    width: 7px; height: 7px; border-radius: 50%; background: var(--blue-primary); color: var(--paper);
    font-size: 4.4px; font-weight: 700; display: inline-flex; align-items: center; justify-content: center;
  }
  .letter-body { position: absolute; left: 30px; top: 133px; width: 285px; }
  .letter-body__salutation { font-size: 8px; margin-bottom: 16px; color: var(--ink); }
  .letter-body p { font-size: 4.8px; line-height: 8.6px; color: var(--ink-soft); text-align: justify; margin-bottom: 8.5px; }
  .letter-body__closing { margin-top: 12px; }
  .signature-area { display: block; width: 62px; height: 26px; margin-top: 9px; border-radius: 3px; background: var(--blue-pale); }

  /* Continuation page */
  .continuation-dot { position: absolute; left: 30px; top: 22px; width: 36px; height: 36px; border-radius: 50%; background: var(--blue-primary); }
</style>
</head>
<body>

<section class="page page--cover" aria-label="Report cover page">
  <svg class="cover-band" viewBox="0 0 337 475" aria-hidden="true">
    <defs>
      <linearGradient id="coverBlue" x1="0" y1="0" x2="0" y2="1">
        <stop offset="0" stop-color="var(--blue-cover-top)" style="stop-color:#0a7fc6"/>
        <stop offset="1" stop-color="var(--blue-cover-bottom)" style="stop-color:#0565a6"/>
      </linearGradient>
    </defs>
    <polygon points="65,8 330,8 330,468 258,468 26,76" fill="url(#coverBlue)"/>
  </svg>
  <div class="cover-brand">
    <span class="cover-brand__dot"></span>
    <span class="cover-brand__name">NORTHVALE SYSTEMS</span>
  </div>
  <h1 class="cover-title">REPORT<br>TITLE HERE</h1>
  <p class="cover-subtitle">YOUR SUBTITLE HERE</p>
  <div class="cover-credit">
    <p class="cover-credit__label">REPORT PREPARED BY</p>
    <p class="cover-credit__name">YOUR NAME HERE</p>
    <div class="cover-dates">
      <div><p class="cover-dates__label">PROPOSAL ISSUED</p><p class="cover-dates__value">SEP 19,2018</p></div>
      <div><p class="cover-dates__label">PROPOSAL VALID TO</p><p class="cover-dates__value">SEP 19,2019</p></div>
    </div>
  </div>
</section>

<section class="page page--letter" aria-label="Letterhead first page">
  <header class="letterhead">
    <span class="letterhead__dot"></span>
    <span class="letterhead__name">NORTHVALE SYSTEMS</span>
    <p class="letterhead__address">NORTHVALE SYSTEMS LLC<br>4120 HARBOR CREST ROAD,<br>JUNEAU, ALASKA 99801</p>
    <ul class="letterhead__contact">
      <li><span class="contact-icon">P</span>555 014 2290</li>
      <li><span class="contact-icon">E</span>INFO@NORTHVALESYSTEMS.COM</li>
      <li><span class="contact-icon">W</span>WWW.NORTHVALESYSTEMS.COM</li>
    </ul>
  </header>
  <article class="letter-body">
    <p class="letter-body__salutation">Dear Mr. Harlow,</p>
    <p>Thank you for meeting with our team last week to discuss the planned upgrade of your network and data services. As promised, this letter sets out the scope we reviewed together, the schedule we proposed for each phase, and the people who will lead the work on our side. We have kept the plan simple so that your staff can follow every step with ease.</p>
    <p>The first phase covers a full audit of your current systems, including servers, storage, user accounts and backup routines. Our engineers will work on site for two days and share a short summary at the end of each day. Any urgent risks will be raised with you straight away, so there are no surprises later in the project.</p>
    <p>In the second phase we will move your core services to the new platform in small, planned stages. Each stage is tested before the next one begins, and your team keeps full access to the old setup until the change is confirmed. We will also provide simple guides and a short training session so that everyone feels confident using the new tools from day one, with support available by phone and email whenever it is needed.</p>
    <p>Please review the enclosed proposal and let us know if you would like to change any part of the plan. We look forward to working with you and will be glad to answer any questions before the project begins.</p>
    <p class="letter-body__closing">Sincerely,</p>
    <span class="signature-area" role="img" aria-label="Handwritten signature of Dana Ellis"></span>
  </article>
</section>

<section class="page page--continuation" aria-label="Letterhead continuation page">
  <span class="continuation-dot"></span>
</section>

</body>
</html>
```